Elegant Business Card for Technology Company

Client is a supplier of innovative industrial communications and automation equipment since 2002. This contest is to gather fresh ideas for a redesign of the existing business card. Client is looking for design that best communicates tagline "Industrial Networking and Computing Specialist".

Design submissions should look modern, clean, elegant and professional. It should not be cluttered. Use white as the primary colour. Orange and black as secondary colour. Refer to jpeg File 1 on the current design.

Fonts used by Client used include Arial Regular, Arial Black, Roboto Regular, Roboto Black and Lato.

The winning design will be sent for offset printing using super white 250gsm artcard paper (open for suggestions).

Target Market(s)

System Engineers, Project Managers, Purchasing Managers from companies providing engineering services for Smart Cities.

Industry/Entity Type

Information Technology

Contact Information for Business Card

Refer to PDF File 3 for Business Card Details. Priority of short contact information would be as follows Name > Job Title > Email > Mobile > Web > Tel > Fax > Business Address >UEN (UEN represents company registration number)

Font styles to use
Sans Serif

Colors
ffffff
f37122
000000
5c5c5c

Requirements
Must have
• Refer to AI File 2 (Company Logo) & PDF File 3 (Information on Namecard)
Should not have
• No QR codes
• No Social Media Icons
• Do not create full Black or Orange colour background

```html
<!DOCTYPE html>
<html lang="en">
<head>
<meta charset="utf-8">
<title>Norvale Business Card</title>
<link rel="stylesheet" href="https://fonts.googleapis.com/css2?family=Lato:wght@400;700;900&display=swap">
<style>
  :root {
    --white: #ffffff;
    --orange: #f37122;
    --black: #000000;
    --ink: #141414;
    --grey: #5c5c5c;
    --backdrop: #e4e4e4;
  }
  * { box-sizing: border-box; margin: 0; padding: 0; }
  html, body { width: 1200px; height: 675px; overflow: hidden; }
  body {
    background: var(--backdrop);
    font-family: "Lato", Arial, sans-serif;
    display: flex;
    align-items: center;
    justify-content: center;
    gap: 40px;
  }
  .card {
    position: relative;
    width: 520px;
    height: 297px;
    overflow: hidden;
    background: var(--white);
    color: var(--ink);
    box-shadow: 0 6px 18px rgba(0,0,0,0.18);
  }
  .brand {
    position: absolute;
    display: flex;
    align-items: center;
    gap: 10px;
  }
  .brand-dot {
    width: 34px; height: 34px;
    border-radius: 50%;
    background: var(--orange);
  }
  .brand-name {
    font-weight: 900;
    font-size: 34px;
    letter-spacing: 1px;
    color: var(--ink);
  }

  /* Front side */
  .card-front .brand { left: 40px; top: 84px; }
  .divider {
    position: absolute;
    left: 262px; top: 66px;
    width: 1px; height: 82px;
    background: var(--grey);
  }
  .services {
    position: absolute;
    left: 280px; top: 66px;
    list-style: none;
    font-size: 11.5px;
    line-height: 16.5px;
    color: var(--ink);
  }
  .services li::before {
    content: "";
    display: inline-block;
    width: 5px; height: 5px;
    border-radius: 50%;
    background: var(--orange);
    margin-right: 6px;
    vertical-align: middle;
  }
  .tagline-band {
    position: absolute;
    left: 0; right: 0; bottom: 0;
    height: 62px;
    background: var(--ink);
    border-top: 4px solid var(--orange);
    display: flex;
    align-items: center;
    justify-content: center;
  }
  .tagline {
    color: var(--white);
    font-size: 14px;
    letter-spacing: 0.3px;
  }

  /* Back side */
  .card-back .brand { right: 34px; top: 36px; }
  .holder {
    position: absolute;
    right: 34px; top: 96px;
    text-align: right;
  }
  .holder-name { font-size: 19px; color: var(--ink); }
  .holder-title { font-size: 12px; color: var(--orange); margin-top: 2px; }
  .contact {
    position: absolute;
    left: 30px; top: 130px;
    font-size: 12px;
    line-height: 15px;
  }
  .company { color: var(--orange); }
  .contact-lines { list-style: none; margin-top: 3px; }
  .contact-lines li { display: flex; align-items: center; gap: 7px; }
  .contact-lines svg { width: 11px; height: 11px; fill: var(--orange); }
  .uen { margin-top: 3px; font-size: 12.5px; }
  .swoosh { position: absolute; inset: 0; width: 100%; height: 100%; }
  .web {
    position: absolute;
    right: 22px; bottom: 16px;
    color: var(--white);
    font-size: 12px;
    letter-spacing: 1px;
  }
</style>
</head>
<body>
  <section class="card card-front" aria-label="Card front">
    <div class="brand">
      <span class="brand-dot"></span>
      <span class="brand-name">NORVALE</span>
    </div>
    <span class="divider"></span>
    <ul class="services">
      <li>Industrial Ethernet / Wireless / Cellular</li>
      <li>Industrial and Embedded Computing</li>
      <li>Serial / Fieldbus Connectivity</li>
      <li>IP Video Surveillance</li>
      <li>Remote Automation</li>
    </ul>
    <div class="tagline-band">
      <p class="tagline">Industrial Networking and Computing Specialist</p>
    </div>
  </section>

  <section class="card card-back" aria-label="Card back">
    <svg class="swoosh" viewBox="0 0 520 297" preserveAspectRatio="none" aria-hidden="true">
      <path d="M110 297 C 280 252, 430 200, 520 140 L520 156 C 430 214, 290 262, 140 297 Z" fill="#f37122"/>
      <path d="M165 297 C 310 262, 440 218, 520 168 L520 297 Z" fill="#141414"/>
    </svg>
    <div class="brand">
      <span class="brand-dot"></span>
      <span class="brand-name">NORVALE</span>
    </div>
    <div class="holder">
      <p class="holder-name">Daniel Lim</p>
      <p class="holder-title">Sales manager</p>
    </div>
    <div class="contact">
      <p class="company">Norvale Asia Pacific Pte Ltd</p>
      <p>24 Kellan Crescent</p>
      <p>Kellan Techpark #05-12 (Lobby B)</p>
      <p>Singapore 401234</p>
      <ul class="contact-lines">
        <li><svg viewBox="0 0 12 12" aria-label="Telephone"><path d="M2 1h3l1 3-1.5 1a6 6 0 0 0 2.5 2.5L8 6l3 1v3a1 1 0 0 1-1 1A9 9 0 0 1 1 2a1 1 0 0 1 1-1z"/></svg>+65 6100 2040</li>
        <li><svg viewBox="0 0 12 12" aria-label="Mobile"><path d="M3 0h6a1 1 0 0 1 1 1v10a1 1 0 0 1-1 1H3a1 1 0 0 1-1-1V1a1 1 0 0 1 1-1zm0 2v7h6V2z"/></svg>+65 8100 3050</li>
        <li><svg viewBox="0 0 12 12" aria-label="Fax"><path d="M3 0h6v3H3zM1 4h10a1 1 0 0 1 1 1v4H9v3H3V9H0V5a1 1 0 0 1 1-1zm3 4v3h4V8z"/></svg>+65 6100 2041</li>
        <li><svg viewBox="0 0 12 12" aria-label="Email"><path d="M0 2h12v1L6 7 0 3zm0 2.2L6 8l6-3.8V10H0z"/></svg>sales@norvale.com.sg</li>
      </ul>
      <p class="uen">UEN No 200900417K</p>
    </div>
    <p class="web">www.norvale.com.sg</p>
  </section>
</body>
</html>
```